USB Flash Drive Catalogue

I would like to make a paper catalogue of the products from our Crafterly store. There are currently 209 items on Crafterly. Some would be excluded. The listings have pricing and would need to be organized a bit different but all the information is there.

https://www.crafterly.com/shop/TurboStickHub/items?ref=pagination&page=1

```html
<!DOCTYPE html>
<html lang="en">
<head>
<meta charset="utf-8">
<title>TurboStickHub Catalog 2017 — Pages 12–13</title>
<link href="https://fonts.googleapis.com/css2?family=PT+Sans:wght@400;700&display=swap" rel="stylesheet">
<style>
:root{
  --orange:#d9822b;
  --orange-dark:#c8701d;
  --charcoal:#545557;
  --ink:#3f4043;
  --text:#4a4b4e;
  --paper:#fbfbfa;
  --backdrop:#dcdcd6;
  --sw1:#4f5a63;--sw2:#868b90;--sw3:#c3c5c7;--sw4:#d9822b;--sw5:#6f9a3e;
}
*{box-sizing:border-box;margin:0;padding:0}
html,body{width:1200px;height:804px;overflow:hidden}
body{background:var(--backdrop);font-family:"PT Sans",sans-serif;color:var(--text)}
.spread{position:absolute;left:60px;top:20px;width:1080px;height:764px;display:flex;box-shadow:0 6px 24px rgba(0,0,0,.18)}
.page{position:relative;width:540px;height:764px;background:linear-gradient(180deg,#fff,var(--paper));overflow:hidden}
.page--left{background:linear-gradient(90deg,#fff 0%,#fbfbfa 88%,#ececea 100%)}
.page--right{background:linear-gradient(90deg,#e9e9e7 0%,#fafaf9 10%,#fff 100%)}
.top-band{position:absolute;top:0;left:0;right:0;height:18px;display:flex}
.top-band .seg-gray{background:var(--charcoal)}
.top-band .seg-orange{background:var(--orange);flex:1}
.page--left .seg-gray{width:48%}
.page--right .seg-gray{width:44%}
.products{position:absolute;top:52px;left:40px;right:40px;display:flex;flex-direction:column;gap:26px}
.product{display:flex;align-items:center;gap:26px;height:196px}
.page--right .product{flex-direction:row-reverse}
.product-frame{width:196px;height:172px;border:1.5px solid var(--orange);border-radius:14px;padding:10px;flex:none}
.product-photo{width:100%;height:100%;border-radius:6px;background:radial-gradient(ellipse at 45% 55%,#e9e2d4 0%,#f3efe7 45%,#fbfaf7 80%)}
.product-info{flex:1}
.product-title{font-size:20px;font-weight:700;color:var(--ink);margin-bottom:8px}
.product-title .accent{color:var(--orange)}
.specs{list-style:none;font-size:9.5px;line-height:1.3}
.specs li{position:relative;padding-left:14px}
.specs li::before{content:"";position:absolute;left:0;top:3px;width:6px;height:6px;background:#333}
.specs li.cont{padding-left:24px}
.specs li.cont::before{display:none}
.price{font-size:11px;font-weight:700;color:var(--ink);margin-top:12px}
.price sup{font-size:7px}
.colors{display:flex;align-items:center;margin-top:4px}
.swatch{width:14px;height:14px;margin-right:2px}
.colors .label{font-size:9px;margin-left:16px}
.footer{position:absolute;left:0;right:0;bottom:0;height:34px;background:var(--orange)}
.footer-tab{position:absolute;bottom:34px;height:26px;background:var(--orange);width:300px;display:flex;align-items:center;justify-content:center;color:#fff;font-size:10.5px}
.page--left .footer-tab{right:40px;border-radius:12px 0 0 0}
.page--right .footer-tab{left:40px;border-radius:0 12px 0 0}
.footer-edition{position:absolute;bottom:10px;color:#fff;font-size:10px;opacity:.9}
.page--left .footer-edition{left:24px}
.page--right .footer-edition{right:24px}
.page-number{position:absolute;bottom:34px;width:40px;height:26px;background:var(--charcoal);color:#fff;font-size:10px;display:flex;align-items:center;justify-content:center}
.page--left .page-number{right:0;border-radius:12px 0 0 0}
.page--right .page-number{left:0;border-radius:0 12px 0 0}
</style>
</head>
<body>
<main class="spread">
  <section class="page page--left">
    <div class="top-band"><div class="seg-gray"></div><div class="seg-orange"></div></div>
    <div class="products">
      <article class="product">
        <div class="product-frame"><div class="product-photo" role="img" aria-label="Engraved maple wooden gift box with wooden USB drive on raffia grass"></div></div>
        <div class="product-info">
          <h2 class="product-title">Antique Maple <span class="accent">Wood</span></h2>
          <ul class="specs">
            <li>Laser Engraved Maple wooden box filled Raffia grass.</li>
            <li>Approximate dimensions: 104 x 96 x 39mm</li>
            <li>16GB maple wood USB drive, Wildwood Body, painted</li>
            <li class="cont">in Wedding White.</li>
            <li>Approximate dimensions: 60 x 28 x 10mm</li>
            <li>Great for artisans, enthusiasts, and gift givers!</li>
            <li>High Quality Korvex Grade Chipset</li>
            <li>Shock resistant and water proof</li>
            <li>USA Company Based in Minneapolis, MN</li>
          </ul>
          <p class="price"><sup>$</sup>25.95</p>
          <div class="colors"><span class="swatch" style="background:var(--sw1)"></span><span class="swatch" style="background:var(--sw2)"></span><span class="swatch" style="background:var(--sw3)"></span><span class="swatch" style="background:var(--sw4)"></span><span class="swatch" style="background:var(--sw5)"></span><span class="label">Available Colors</span></div>
        </div>
      </article>
      <article class="product">
        <div class="product-frame"><div class="product-photo" role="img" aria-label="Engraved maple wooden gift box with wooden USB drive on raffia grass"></div></div>
        <div class="product-info">
          <h2 class="product-title">Antique Maple <span class="accent">Wood</span></h2>
          <ul class="specs">
            <li>Laser Engraved Maple wooden box filled Raffia grass.</li>
            <li>Approximate dimensions: 104 x 96 x 39mm</li>
            <li>16GB maple wood USB drive, Wildwood Body, painted</li>
            <li class="cont">in Wedding White.</li>
            <li>Approximate dimensions: 60 x 28 x 10mm</li>
            <li>Great for artisans, enthusiasts, and gift givers!</li>
            <li>High Quality Korvex Grade Chipset</li>
            <li>Shock resistant and water proof</li>
            <li>USA Company Based in Minneapolis, MN</li>
          </ul>
          <p class="price"><sup>$</sup>25.95</p>
          <div class="colors"><span class="swatch" style="background:var(--sw1)"></span><span class="swatch" style="background:var(--sw2)"></span><span class="swatch" style="background:var(--sw3)"></span><span class="swatch" style="background:var(--sw4)"></span><span class="swatch" style="background:var(--sw5)"></span><span class="label">Available Colors</span></div>
        </div>
      </article>
      <article class="product">
        <div class="product-frame"><div class="product-photo" role="img" aria-label="Engraved maple wooden gift box with wooden USB drive on raffia grass"></div></div>
        <div class="product-info">
          <h2 class="product-title">Antique Maple <span class="accent">Wood</span></h2>
          <ul class="specs">
            <li>Laser Engraved Maple wooden box filled Raffia grass.</li>
            <li>Approximate dimensions: 104 x 96 x 39mm</li>
            <li>16GB maple wood USB drive, Wildwood Body, painted</li>
            <li class="cont">in Wedding White.</li>
            <li>Approximate dimensions: 60 x 28 x 10mm</li>
            <li>Great for artisans, enthusiasts, and gift givers!</li>
            <li>High Quality Korvex Grade Chipset</li>
            <li>Shock resistant and water proof</li>
            <li>USA Company Based in Minneapolis, MN</li>
          </ul>
          <p class="price"><sup>$</sup>25.95</p>
          <div class="colors"><span class="swatch" style="background:var(--sw1)"></span><span class="swatch" style="background:var(--sw2)"></span><span class="swatch" style="background:var(--sw3)"></span><span class="swatch" style="background:var(--sw4)"></span><span class="swatch" style="background:var(--sw5)"></span><span class="label">Available Colors</span></div>
        </div>
      </article>
    </div>
    <div class="footer-tab">Call us 800-555-0147 | www.crafterly.com/shop/TurboStickHub</div>
    <div class="page-number">12</div>
    <footer class="footer"><span class="footer-edition">Catalog 2017</span></footer>
  </section>

  <section class="page page--right">
    <div class="top-band"><div class="seg-gray"></div><div class="seg-orange"></div></div>
    <div class="products">
      <article class="product">
        <div class="product-frame"><div class="product-photo" role="img" aria-label="Engraved maple wooden gift box with wooden USB drive on raffia grass"></div></div>
        <div class="product-info">
          <h2 class="product-title">Antique Maple <span class="accent">Wood</span></h2>
          <ul class="specs">
            <li>Laser Engraved Maple wooden box filled Raffia grass.</li>
            <li>Approximate dimensions: 104 x 96 x 39mm</li>
            <li>16GB maple wood USB drive, Wildwood Body, painted</li>
            <li class="cont">in Wedding White.</li>
            <li>Approximate dimensions: 60 x 28 x 10mm</li>
            <li>Great for artisans, enthusiasts, and gift givers!</li>
            <li>High Quality Korvex Grade Chipset</li>
            <li>Shock resistant and water proof</li>
            <li>USA Company Based in Minneapolis, MN</li>
          </ul>
          <p class="price"><sup>$</sup>25.95</p>
          <div class="colors"><span class="swatch" style="background:var(--sw1)"></span><span class="swatch" style="background:var(--sw2)"></span><span class="swatch" style="background:var(--sw3)"></span><span class="swatch" style="background:var(--sw4)"></span><span class="swatch" style="background:var(--sw5)"></span><span class="label">Available Colors</span></div>
        </div>
      </article>
      <article class="product">
        <div class="product-frame"><div class="product-photo" role="img" aria-label="Engraved maple wooden gift box with wooden USB drive on raffia grass"></div></div>
        <div class="product-info">
          <h2 class="product-title">Antique Maple <span class="accent">Wood</span></h2>
          <ul class="specs">
            <li>Laser Engraved Maple wooden box filled Raffia grass.</li>
            <li>Approximate dimensions: 104 x 96 x 39mm</li>
            <li>16GB maple wood USB drive, Wildwood Body, painted</li>
            <li class="cont">in Wedding White.</li>
            <li>Approximate dimensions: 60 x 28 x 10mm</li>
            <li>Great for artisans, enthusiasts, and gift givers!</li>
            <li>High Quality Korvex Grade Chipset</li>
            <li>Shock resistant and water proof</li>
            <li>USA Company Based in Minneapolis, MN</li>
          </ul>
          <p class="price"><sup>$</sup>25.95</p>
          <div class="colors"><span class="swatch" style="background:var(--sw1)"></span><span class="swatch" style="background:var(--sw2)"></span><span class="swatch" style="background:var(--sw3)"></span><span class="swatch" style="background:var(--sw4)"></span><span class="swatch" style="background:var(--sw5)"></span><span class="label">Available Colors</span></div>
        </div>
      </article>
      <article class="product">
        <div class="product-frame"><div class="product-photo" role="img" aria-label="Engraved maple wooden gift box with wooden USB drive on raffia grass"></div></div>
        <div class="product-info">
          <h2 class="product-title">Antique Maple <span class="accent">Wood</span></h2>
          <ul class="specs">
            <li>Laser Engraved Maple wooden box filled Raffia grass.</li>
            <li>Approximate dimensions: 104 x 96 x 39mm</li>
            <li>16GB maple wood USB drive, Wildwood Body, painted</li>
            <li class="cont">in Wedding White.</li>
            <li>Approximate dimensions: 60 x 28 x 10mm</li>
            <li>Great for artisans, enthusiasts, and gift givers!</li>
            <li>High Quality Korvex Grade Chipset</li>
            <li>Shock resistant and water proof</li>
            <li>USA Company Based in Minneapolis, MN</li>
          </ul>
          <p class="price"><sup>$</sup>25.95</p>
          <div class="colors"><span class="swatch" style="background:var(--sw1)"></span><span class="swatch" style="background:var(--sw2)"></span><span class="swatch" style="background:var(--sw3)"></span><span class="swatch" style="background:var(--sw4)"></span><span class="swatch" style="background:var(--sw5)"></span><span class="label">Available Colors</span></div>
        </div>
      </article>
    </div>
    <div class="page-number">13</div>
    <div class="footer-tab">Call us 800-555-0147 | www.crafterly.com/shop/TurboStickHub</div>
    <footer class="footer"><span class="footer-edition">Catalog 2017</span></footer>
  </section>
</main>
</body>
</html>
```